Landscape design build company door flyer

I would like this flyer to convey a high-level of professionalism for a company that is excellent with communication with their clients as well as a company that does incredible installations

Went on vacation/holiday

```html
<!DOCTYPE html>
<html lang="en">
<head>
<meta charset="utf-8">
<title>Cedar Ridge Builders – Outdoor Living Flyer</title>
<link rel="stylesheet" href="https://fonts.googleapis.com/css2?family=Montserrat:wght@400;500;600;700;800;900&display=swap">
<style>
  :root{
    --navy:#15304a;
    --gold:#f5ab10;
    --white:#ffffff;
    --tab-grey:#ececec;
    --stage:#e8e8e8;
    --ink:#15304a;
  }
  *{margin:0;padding:0;box-sizing:border-box}
  html,body{width:1200px;height:1029px;overflow:hidden;background:var(--stage);font-family:"Montserrat",sans-serif}
  .flyer{position:absolute;left:211px;top:14px;width:778px;height:1000px;background:var(--white);overflow:hidden}
  .hero{position:absolute;left:0;top:50px;width:778px;height:653px;background:var(--navy);overflow:hidden}
  .brand-tab{position:absolute;left:0;top:0;width:778px;height:170px}
  .brand{position:absolute;left:292px;top:0;width:185px;height:137px;display:flex;flex-direction:column;align-items:center;justify-content:center;gap:10px;text-align:center}
  .brand-dot{width:34px;height:34px;border-radius:50%;background:var(--navy)}
  .brand-name{font-weight:700;font-size:14px;line-height:1.2;color:var(--navy);letter-spacing:.5px}
  .headline{position:absolute;left:0;top:119px;width:778px;text-align:center;font-weight:800;font-size:44px;line-height:47px;color:var(--white);letter-spacing:.3px}
  .headline .accent{color:var(--gold);display:block}
  .about{position:absolute;left:61px;top:304px;width:271px;color:var(--white)}
  .section-title{font-weight:600;font-size:18px;line-height:22px;letter-spacing:.3px}
  .about p{font-weight:500;font-size:11.4px;line-height:14.8px;text-align:justify;hyphens:auto;margin-top:10px;width:271px}
  .about p + p{margin-top:14px}
  .photo{position:absolute}
  .photo.deck{left:369px;top:306px;width:130px;height:130px;background:linear-gradient(160deg,#5f8a45 0%,#8a4a2c 55%,#6b3520 100%)}
  .photo.pavilion{left:510px;top:306px;width:208px;height:130px;background:linear-gradient(180deg,#7a5a3c 0%,#4b4b4b 50%,#707070 100%)}
  .photo.pool{left:369px;top:446px;width:130px;height:91px;background:linear-gradient(180deg,#d9dcd5 0%,#9bb39a 45%,#4fb3a7 100%)}
  .photo.steps{left:369px;top:546px;width:130px;height:91px;background:linear-gradient(180deg,#6f6a5c 0%,#8a8d90 45%,#5b5e62 100%)}
  .photo.firepit{left:510px;top:446px;width:208px;height:191px;background:linear-gradient(180deg,#3b6fb8 0%,#2d5288 35%,#1e2e4a 58%,#3a3a4a 80%,#2a2630 100%)}
  .services{position:absolute;left:61px;top:713px;color:var(--ink)}
  .service-list{position:absolute;left:0;top:0;width:778px;height:160px;list-style:none}
  .service{position:absolute;display:flex;align-items:center;gap:9px;font-weight:600;font-size:11.4px;color:var(--ink);letter-spacing:.2px}
  .service svg{width:27px;height:27px;flex:none}
  .seal{position:absolute;left:600px;top:737px;width:117px;height:117px;border-radius:50%;background:radial-gradient(circle at 40% 35%,#f7d25a 0%,#d9a81e 55%,#a97a0c 100%);box-shadow:inset 0 0 0 5px #8a6208,inset 0 0 0 9px #e8c043}
  .contact{position:absolute;left:0;top:876px;width:778px;height:118px;background:var(--navy)}
  .contact-title{position:absolute;left:61px;top:16px;font-weight:600;font-size:16px;color:var(--white);letter-spacing:.3px}
  .phone{position:absolute;left:61px;top:40px;display:flex;align-items:center;gap:14px;font-weight:600;font-size:42px;color:var(--gold);letter-spacing:.5px}
  .phone svg{width:38px;height:38px}
  .email{position:absolute;right:30px;top:49px;font-weight:400;font-size:16px;color:var(--white)}
</style>
</head>
<body>
<main class="flyer">
  <section class="hero">
    <h1 class="headline">LET’S CREATE<span class="accent">YOUR DREAM OUTDOOR</span>LIVING SPACE!</h1>

    <div class="about">
      <h2 class="section-title">ABOUT US</h2>
      <p>Discover the endless possibilities for your outdoor space with The Cedar Ridge Builders Team. Our team of skilled artisans is dedicated to turning your outdoor space into a breathtaking oasis that you’ll love coming home to. Whether it’s a cozy patio for intimate gatherings, a sprawling deck to host memorable parties, or a custom paver driveway that adds instant curb appeal, our high-quality craftsmanship ensures stunning results that exceed your expectations.</p>
      <p>From concept to completion, we take pride in every detail, using the finest materials to withstand Seattle’s climate while adding timeless elegance to your property. Embrace the Pacific Northwest lifestyle and create cherished moments with family and friends in a captivating outdoor haven.</p>
    </div>

    <div class="photo deck" role="img" aria-label="Wooden deck with pergola and patio chairs"></div>
    <div class="photo pavilion" role="img" aria-label="Covered pavilion with stone outdoor fireplace"></div>
    <div class="photo pool" role="img" aria-label="Backyard swimming pool beside a modern home"></div>
    <div class="photo steps" role="img" aria-label="Stone retaining wall with steps"></div>
    <div class="photo firepit" role="img" aria-label="Paver patio with fire pit and chairs overlooking a lake at dusk"></div>
  </section>

  <svg class="brand-tab" viewBox="0 0 778 170" aria-hidden="true">
    <rect x="229" y="0" width="314" height="50" fill="var(--tab-grey)"/>
    <polygon points="229,50 543,50 477,137 292,137" fill="var(--tab-grey)"/>
    <rect x="292" y="0" width="185" height="137" fill="var(--white)"/>
    <line x1="292" y1="137" x2="292" y2="170" stroke="#0b1c2c" stroke-width="1"/>
    <line x1="477" y1="137" x2="477" y2="170" stroke="#0b1c2c" stroke-width="1"/>
  </svg>
  <div class="brand">
    <span class="brand-dot"></span>
    <span class="brand-name">CEDAR RIDGE BUILDERS</span>
  </div>

  <section class="services">
    <h2 class="section-title">OUR SERVICES</h2>
  </section>
  <ul class="service-list">
    <li class="service" style="left:63px;top:756px">
      <svg viewBox="0 0 28 28"><path d="M3 12 14 3l11 9v14H3z" fill="none" stroke="var(--navy)" stroke-width="2"/><path d="M8 16h12M10 16v6M18 16v6M14 11v5" stroke="var(--navy)" stroke-width="1.8"/></svg>Paver Patios</li>
    <li class="service" style="left:63px;top:795px">
      <svg viewBox="0 0 28 28"><path d="M3 12 14 3l11 9v14H3z" fill="none" stroke="var(--navy)" stroke-width="2"/><path d="M6 22l4-7h8l4 7z" fill="var(--navy)"/></svg>Paver Driveways</li>
    <li class="service" style="left:63px;top:836px">
      <svg viewBox="0 0 28 28"><path d="M3 12 14 3l11 9v14H3z" fill="none" stroke="var(--navy)" stroke-width="2"/><path d="M8 13h10v3H8zM10 17h10v3H10z" fill="var(--navy)"/></svg>Retaining Walls</li>
    <li class="service" style="left:229px;top:756px">
      <svg viewBox="0 0 28 28"><path d="M3 12 14 3l11 9v14H3z" fill="none" stroke="var(--navy)" stroke-width="2"/><path d="M10 10v8M17 10v8M10 13h7M7 20c2-1.5 3 1.5 5 0s3 1.5 5 0 3 1.5 4 0" fill="none" stroke="var(--navy)" stroke-width="1.6"/></svg>Pools</li>
    <li class="service" style="left:229px;top:795px">
      <svg viewBox="0 0 28 28"><path d="M3 12 14 3l11 9v14H3z" fill="none" stroke="var(--navy)" stroke-width="2"/><path d="M7 14h14M8 14v8M20 14v8M12 14v8M16 14v8M7 22h14" stroke="var(--navy)" stroke-width="1.6"/></svg>Decks &amp; Railings</li>
    <li class="service" style="left:229px;top:836px">
      <svg viewBox="0 0 28 28"><path d="M3 12 14 3l11 9v14H3z" fill="none" stroke="var(--navy)" stroke-width="2"/><path d="M8 22v-6l6-5 6 5v6z" fill="var(--navy)"/><path d="M14 21c-2 0-2-2 0-4 2 2 2 4 0 4z" fill="var(--white)"/></svg>Firepits &amp; Fireplaces</li>
    <li class="service" style="left:400px;top:756px">
      <svg viewBox="0 0 28 28"><path d="M3 12 14 3l11 9v14H3z" fill="none" stroke="var(--navy)" stroke-width="2"/><path d="M12 11h4l-1 6h-2zM14 17v5" fill="none" stroke="var(--navy)" stroke-width="1.6"/></svg>Outdoor Lighting</li>
    <li class="service" style="left:400px;top:795px">
      <svg viewBox="0 0 28 28"><path d="M3 12 14 3l11 9v14H3z" fill="none" stroke="var(--navy)" stroke-width="2"/><circle cx="14" cy="17" r="5" fill="none" stroke="var(--navy)" stroke-width="1.4"/><path d="M14 14v6M11 17h6" stroke="var(--navy)" stroke-width="1.4"/></svg>And More...</li>
  </ul>
  <div class="seal" role="img" aria-label="Experience seal"></div>

  <section class="contact">
    <h2 class="contact-title">CONTACT US TODAY</h2>
    <div class="phone">
      <svg viewBox="0 0 40 40" aria-hidden="true"><path d="M9 4l6 1 3 8-4 3c2 5 6 9 11 11l3-4 8 3 1 6c-1 3-4 5-7 5C17 37 3 23 3 10c0-3 3-6 6-6z" fill="var(--gold)"/><path d="M23 6a12 12 0 0 1 11 11M22 12a6 6 0 0 1 6 6" fill="none" stroke="var(--gold)" stroke-width="2.6" stroke-linecap="round"/></svg>
      <span>[206]-555-0148</span>
    </div>
    <span class="email">info@cedarridgebuilders.com</span>
  </section>
</main>
</body>
</html>
```